KAJU Freightways #ALLKAJU Business Cards & Letterhead

I am looking to business cards designed for our organization. We are currently undergoing a small re-branding that is taking place. Our organization is called KAJU Freightways and we are headquartered in Phoenix, AZ. We primarily provide transportation and logistics services to the Marlow Parcel Bureau who is our largest customer. I would like to see a design that incorporates name, title, contact info, website, and address (this will be different depending on the employee). I would also like to see some color on the business card using our logo colors or a variation. I would like our logo on the back of the business card with the website displayed. The final design should communicate that we are a next generation transportation operate that focuses on being driver-first, customer-centric, innovative, and sustainable.We would also like our #ALLKAJU catch phrase incorporated as well.

Target Market(s)

Transportation & Logistics

Industry/Entity Type

Trucking Company

Contact Information for Business Card

-First and Last Name
-Position Title
-Contact Phone
-Contact Email
-Physical Address

Font styles to use
Serif

Colors

Designer to choose colors to be used in the design.

Requirements
Must have
• -KAJU logo prominently displayed
• -#ALLKAJU catch phrase used
• -Some amount of color, design gradient, etc.
• -Logo on the back with website listed (https://www.kajufreightco.example)

```html
<!DOCTYPE html>
<html lang="en">
<head>
<meta charset="utf-8">
<title>KAJU Freightways – Letterhead &amp; Business Cards</title>
<link href="https://fonts.googleapis.com/css2?family=Lato:wght@400;700;900&family=Arimo:wght@400;700&display=swap" rel="stylesheet">
<style>
  :root {
    --navy: #133a45;
    --green: #7ab843;
    --paper: #f5f5f5;
    --ink: #1b1b1b;
    --backdrop: #e3e3e3;
  }
  * { margin: 0; padding: 0; box-sizing: border-box; }
  html, body { width: 1200px; height: 1200px; overflow: hidden; }
  body { background: var(--backdrop); position: relative; font-family: 'Lato', sans-serif; color: var(--navy); }

  /* ---------- Letterhead ---------- */
  .letterhead { position: absolute; left: 88px; top: 147px; width: 696px; height: 900px; background: var(--paper); }
  .letterhead .edge-band { position: absolute; left: 0; top: 0; }
  .letterhead .tab { position: absolute; left: 686px; top: 50px; width: 10px; height: 78px; background: var(--navy); }

  .brand { position: absolute; display: flex; align-items: center; gap: 7px; }
  .brand .wordmark { font-family: 'Lato', sans-serif; font-weight: 900; color: var(--navy); letter-spacing: 0.02em; }
  .brand .dot { border: 3px solid var(--green); border-radius: 50%; }
  .letterhead .brand { left: 62px; top: 70px; }
  .letterhead .brand .wordmark { font-size: 34px; }
  .letterhead .brand .dot { width: 20px; height: 20px; }

  .divider { position: absolute; width: 2px; background: var(--navy); }
  .letterhead .divider { left: 175px; top: 42px; height: 95px; }
  .tagline { position: absolute; color: var(--green); font-weight: 400; line-height: 1.2; }
  .letterhead .tagline { left: 191px; top: 69px; font-size: 17px; }

  .contact { position: absolute; text-align: right; color: var(--navy); }
  .letterhead .contact { right: 49px; top: 49px; font-size: 10px; line-height: 12.4px; }
  .contact .company { font-weight: 700; }
  .contact .gap { height: 6px; }
  .contact .row { display: flex; justify-content: flex-end; align-items: center; gap: 3px; }
  .contact svg { display: block; flex: none; }

  .letter { position: absolute; left: 66px; width: 581px; font-family: 'Arimo', sans-serif; font-size: 10px; line-height: 13.7px; color: var(--ink); }
  .letter.date { top: 229px; }
  .letter.recipient { top: 256px; }
  .letter.salutation { top: 353px; font-weight: 700; }
  .letter.body { top: 394px; text-align: justify; }
  .letter.body p { margin-bottom: 13.7px; }
  .letter.closing { top: 694px; }
  .signature { position: absolute; left: 66px; top: 730px; width: 140px; height: 22px; background: linear-gradient(90deg, rgba(27,27,27,0.14), rgba(27,27,27,0.04)); border-radius: 3px; }
  .letter.signer { top: 762px; }
  .hashtag { position: absolute; font-weight: 700; color: var(--navy); letter-spacing: 0.12em; }
  .hashtag .mark { color: var(--green); }
  .letterhead .hashtag { left: 66px; top: 853px; font-size: 11px; }

  /* ---------- Business card: back ---------- */
  .card { position: absolute; width: 286px; height: 164px; }
  .card-back { left: 837px; top: 273px; background: var(--navy); }
  .card-back .brand { left: 22px; top: 66px; }
  .card-back .brand .wordmark { font-size: 24px; color: #ffffff; }
  .card-back .brand .dot { width: 14px; height: 14px; border-width: 2px; }
  .card-back .divider { left: 126px; top: 52px; height: 60px; width: 1.5px; background: #ffffff; }
  .card-back .tagline { left: 136px; top: 70px; font-size: 10px; }
  .card-back .url { position: absolute; left: 0; right: 0; top: 139px; text-align: center; font-size: 7px; letter-spacing: 0.14em; color: #ffffff; }
  .card-back .url .accent { color: var(--green); }

  /* ---------- Business card: front ---------- */
  .card-front { left: 837px; top: 461px; background: var(--paper); }
  .card-front .edge-band { position: absolute; left: 0; top: 0; }
  .card-front .brand { left: 16px; top: 34px; }
  .card-front .brand .wordmark { font-size: 19px; }
  .card-front .brand .dot { width: 11px; height: 11px; border-width: 2px; }
  .card-front .tab { position: absolute; left: 279px; top: 34px; width: 7px; height: 21px; background: var(--navy); }
  .card-front .person { position: absolute; right: 21px; top: 35px; text-align: right; }
  .card-front .person .name { font-size: 10.5px; color: var(--green); letter-spacing: 0.02em; line-height: 12px; }
  .card-front .person .title { font-size: 7px; line-height: 9px; }
  .card-front .contact { right: 21px; top: 85px; font-size: 7px; line-height: 9.4px; }
  .card-front .contact .gap { height: 6px; }
  .card-front .hashtag { left: 33px; top: 127px; font-size: 7px; }
</style>
</head>
<body>

<!-- Letterhead -->
<section class="letterhead" aria-label="Letterhead">
  <svg class="edge-band" width="17" height="900" viewBox="0 0 17 900" aria-hidden="true">
    <polygon points="0,0 17,0 17,795 0,787" fill="#133a45"/>
    <polygon points="0,791 17,799 17,900 0,900" fill="#7ab843"/>
  </svg>
  <div class="tab"></div>

  <div class="brand"><span class="wordmark">KAJU</span><span class="dot"></span></div>
  <div class="divider"></div>
  <div class="tagline">Transportation<br>and Energy Services</div>

  <address class="contact" style="font-style:normal">
    <div class="company">KAJU Freightways &amp; Energy Services, Inc.</div>
    <div>4170 North Cactus Ridge Road</div>
    <div>Glendale, AZ 85301</div>
    <div class="gap"></div>
    <div class="row">602-555-0148
      <svg width="8" height="8" viewBox="0 0 24 24"><path fill="#7ab843" d="M6.6 10.8c1.4 2.8 3.8 5.1 6.6 6.6l2.2-2.2c.3-.3.7-.4 1-.2 1.1.4 2.3.6 3.6.6.6 0 1 .4 1 1V20c0 .6-.4 1-1 1C10.6 21 3 13.4 3 4c0-.6.4-1 1-1h3.5c.6 0 1 .4 1 1 0 1.3.2 2.5.6 3.6.1.3 0 .7-.2 1z"/></svg></div>
    <div class="row">info@kajufreightco.example
      <svg width="8" height="8" viewBox="0 0 24 24"><rect x="2" y="5" width="20" height="14" fill="none" stroke="#7ab843" stroke-width="2.5"/><path d="M2 5l10 8 10-8" fill="none" stroke="#7ab843" stroke-width="2.5"/></svg></div>
    <div class="row">www.kajufreightco.example
      <svg width="8" height="8" viewBox="0 0 24 24"><circle cx="12" cy="12" r="10" fill="none" stroke="#7ab843" stroke-width="2.5"/><ellipse cx="12" cy="12" rx="4.5" ry="10" fill="none" stroke="#7ab843" stroke-width="2"/><path d="M2 12h20" stroke="#7ab843" stroke-width="2"/></svg></div>
  </address>

  <div class="letter date">November 15, 2019</div>
  <div class="letter recipient">Mr. John Doe<br>President<br>AA Corporation<br>111 Street Name, Suite#<br>City, State, 12345</div>
  <div class="letter salutation">Dear Mr. John,</div>
  <div class="letter body">
    <p>Lorem ipsum dolor sit amet, consectetur adipiscing elit. Integer diam quam, egestas eu ultrices eu, suscipit ac sapien. Phasellus eu dui nisi. Nam et euismod diam, nec lobortis tortor. Donec et diam nulla. Aenean varius tincidunt convallis. Aliquam a tortor at lacus dictum aliquet. Nunc laoreet metus sapien, in scelerisque augue consectetur in.</p>
    <p>Fusce nec justo laoreet, egestas justo sed, aliquet sem. Pellentesque pharetra massa non orci bibendum semper. Pellentesque cursus eu lectus a consectetur. Nunc volutpat suscipit posuere. Vestibulum facilisis vel quam malesuada mattis. Nulla in mattis tellus. Maecenas tristique mauris vitae pharetra tincidunt. In ut ornare risus. Integer molestie vestibulum nisi, semper dapibus mi condimentum eu.</p>
    <p>Nullam sagittis elit libero, id fringilla est tincidunt eget. Donec in ipsum ultricies, consectetur quam vel, facilisis elit. Phasellus tincidunt congue risus vel luctus. Suspendisse ut mollis neque. Donec ornare orci in turpis vestibulum, in ultrices metus scelerisque. Pellentesque mattis mattis nunc, nec tincidunt lacus egestas id. Fusce facilisis sagittis neque sit amet vulputate. Aliquam ut eros lobortis tortor facilisis vehicula. Sed sed luctus leo, at laoreet sapien. Donec placerat adipiscing ligula non euismod. In lobortis pretium nisl id luctus.</p>
    <p>Integer gravida tincidunt nibh, scelerisque tincidunt turpis. Suspendisse potenti. Nunc hendrerit euismod lectus id elementum. Fusce vitae gravida velit, quis eleifend lectus. In imperdiet mauris eu dui viverra sagittis. Donec tempor dui diam, condimentum gravida lacus pretium a. Nullam fringilla augue quis arcu placerat scelerisque. Aliquam nec tincidunt augue, sit amet posuere ipsum.</p>
  </div>
  <div class="letter closing">Sincerely Yours,</div>
  <div class="signature" role="img" aria-label="Handwritten signature of Reyna Halvorsen"></div>
  <div class="letter signer">Reyna Halvorsen<br>President</div>
  <div class="hashtag"><span class="mark">#</span>ALLKAJU</div>
</section>

<!-- Business card back -->
<section class="card card-back" aria-label="Business card back">
  <div class="brand"><span class="wordmark">KAJU</span><span class="dot"></span></div>
  <div class="divider"></div>
  <div class="tagline">Transportation<br>and Energy Services</div>
  <div class="url">www.<span class="accent">kajufreightco</span>.example</div>
</section>

<!-- Business card front -->
<section class="card card-front" aria-label="Business card front">
  <svg class="edge-band" width="7" height="164" viewBox="0 0 7 164" aria-hidden="true">
    <polygon points="0,0 7,0 7,126 0,122" fill="#133a45"/>
    <polygon points="0,125 7,129 7,164 0,164" fill="#7ab843"/>
  </svg>
  <div class="tab"></div>
  <div class="brand"><span class="wordmark">KAJU</span><span class="dot"></span></div>
  <div class="person">
    <div class="name">REYNA HALVORSEN</div>
    <div class="title">President</div>
  </div>
  <address class="contact" style="font-style:normal">
    <div class="company">KAJU Freightways &amp; Energy Services, Inc.</div>
    <div>4170 North Cactus Ridge Road</div>
    <div>Glendale, AZ 85301</div>
    <div class="gap"></div>
    <div class="row">602-555-0148
      <svg width="6" height="6" viewBox="0 0 24 24"><path fill="#7ab843" d="M6.6 10.8c1.4 2.8 3.8 5.1 6.6 6.6l2.2-2.2c.3-.3.7-.4 1-.2 1.1.4 2.3.6 3.6.6.6 0 1 .4 1 1V20c0 .6-.4 1-1 1C10.6 21 3 13.4 3 4c0-.6.4-1 1-1h3.5c.6 0 1 .4 1 1 0 1.3.2 2.5.6 3.6.1.3 0 .7-.2 1z"/></svg></div>
    <div class="row">reyna@kajufreightco.example
      <svg width="6" height="6" viewBox="0 0 24 24"><rect x="2" y="5" width="20" height="14" fill="none" stroke="#7ab843" stroke-width="2.5"/><path d="M2 5l10 8 10-8" fill="none" stroke="#7ab843" stroke-width="2.5"/></svg></div>
    <div class="row">www.kajufreightco.example
      <svg width="6" height="6" viewBox="0 0 24 24"><circle cx="12" cy="12" r="10" fill="none" stroke="#7ab843" stroke-width="2.5"/><ellipse cx="12" cy="12" rx="4.5" ry="10" fill="none" stroke="#7ab843" stroke-width="2"/><path d="M2 12h20" stroke="#7ab843" stroke-width="2"/></svg></div>
  </address>
  <div class="hashtag"><span class="mark">#</span>ALLKAJU</div>
</section>

</body>
</html>
```